Mobile app for checking bus arrival

I would like to make the UI much more beautiful and modern. The app is an app to check bus arrival in Singapore.
See here: https://apps.veltrano.com/store/apps/details?id=com.ridoka&hl=en

Based on the question from designers:

1. The first screen shows the favorite bus stop. Each item shows location / street, the top one is the location, second line is the street name. And the number is the bus stop code.

2. Please download the app and try bus stop code with 07589 or 10079, for example. It will bring you to the next screen.

3. The pencil allow you to select color theme, for the list item, and the header.

4. On the second screen, it will show up the list of bus route that available on that bus stop.

5. When you tap on one of them it will show you the 2 subsequent arrival time.

6. Each of the arrival time has the information of availability seats available, seats not available, no more space. (we can use green, yellow, red, respectively).

7. Each of the arrival time has the WAB indicator (Wheelchair availability). Show as icon is preferred.

7. KLT and VOPN are the bus provider in Singapore. 48 means the route /service no.

Requirements:
And check the attachment, see screen 3. I need to add information about the space availability, which has 3 state: seats available, seats not available, no more space. (we can use green, yellow, red, respectively).

Please advise how to show the information.

Target Market(s)

Students, age below 35

Industry/Entity Type

Trivex

Requirements
Must have
• The app currently has the capabilities to select color theme, checkout screen1. It's the button and the list item color.
Nice to have
• Please download the app to see all available colors, and make suggestion to have better color pallete.

```html
<!DOCTYPE html>
<html lang="en">
<head>
<meta charset="utf-8">
<title>Bus Arrival – Stop 07589</title>
<link rel="stylesheet" href="https://fonts.googleapis.com/css2?family=Quicksand:wght@400;500;600;700&display=swap">
<style>
  :root{
    --bg:#e9e8e4;
    --red:#e5524a;
    --red-dark:#d8453d;
    --teal:#22c3d3;
    --blue:#1ea4ec;
    --purple:#9b37b3;
    --grey-tile:#d6d6d6;
    --grey-text:#5b5b5b;
    --paper:#f6f2f2;
    --white:#ffffff;
    --dot:#9c9c9c;
    --dot-red:#e23b3b;
    --dot-yellow:#f2c200;
    --ad-dark:#3a2a12;
    --ad-gold:#c98a1e;
  }
  *{box-sizing:border-box;margin:0;padding:0}
  html,body{width:1200px;height:789px;overflow:hidden;background:var(--bg);
    font-family:"Quicksand",sans-serif}
  .canvas{width:1200px;height:789px;display:flex;align-items:center;justify-content:center}
  .screen{width:400px;height:711px;background:var(--white);position:relative;overflow:hidden;
    box-shadow:0 8px 30px rgba(0,0,0,.12)}

  .status-bar{height:22px;background:var(--red);color:var(--white);font-size:11px;font-weight:600;
    display:flex;align-items:center;justify-content:space-between;padding:0 8px}
  .status-left,.status-right{display:flex;align-items:center;gap:4px}
  .status-time{position:absolute;left:50%;transform:translateX(-50%)}

  .app-bar{background:var(--red);color:var(--white)}
  .app-bar-top{height:40px;display:flex;align-items:center;gap:18px;padding:0 14px}
  .stop-code{font-size:19px;font-weight:500;letter-spacing:1px}
  .app-bar-bottom{display:flex;align-items:stretch;height:56px}
  .stop-info{flex:1;background:var(--paper);padding:8px 14px;color:#333}
  .stop-name{font-size:20px;font-weight:500;line-height:1.1}
  .stop-street{font-size:11px;color:#888}
  .stop-actions{width:118px;display:flex;align-items:center;justify-content:space-around;padding:0 6px}

  .route-grid{display:grid;grid-template-columns:1fr 1fr;gap:6px;padding:6px}
  .column{display:flex;flex-direction:column;gap:6px}
  .tile{height:176px;display:flex;flex-direction:column;align-items:center;justify-content:center;color:var(--white)}
  .tile-number{font-size:46px;font-weight:600;line-height:1}
  .tile-operator{font-size:16px;font-weight:600;letter-spacing:1px}
  .tile--red{background:var(--red)}
  .tile--purple{background:var(--purple)}
  .tile--grey{background:var(--grey-tile);color:var(--grey-text)}

  .route-card{background:var(--white);box-shadow:0 1px 3px rgba(0,0,0,.2)}
  .route-card-head{height:30px;background:var(--red);color:var(--white);display:flex;align-items:center;padding:0 8px;position:relative}
  .route-card-head .route-number{position:absolute;left:0;right:0;text-align:center;font-size:22px;font-weight:600}
  .arrivals{display:flex;gap:10px;padding:10px 10px 4px}
  .arrival{flex:1;display:flex;flex-direction:column;align-items:center;gap:6px}
  .arrival-minutes{width:100%;height:58px;display:flex;align-items:center;justify-content:center;
    color:var(--white);font-size:32px;font-weight:600;border-radius:2px}
  .arrival-minutes--next{background:var(--teal)}
  .arrival-minutes--later{background:var(--blue)}
  .arrival-meta{display:flex;align-items:center;gap:5px;padding-bottom:6px}
  .load-dot{width:7px;height:7px;border-radius:50%;background:var(--dot)}
  .load-dot--red{background:var(--dot-red)}
  .load-dot--yellow{background:var(--dot-yellow)}

  .ad-banner{position:absolute;left:0;right:0;bottom:0;height:62px;
    background:linear-gradient(90deg,var(--ad-dark) 0%,#6b4813 35%,var(--ad-gold) 60%,#8a5a14 100%);
    display:flex;align-items:center;justify-content:space-between;padding:0 16px 0 22px;color:var(--white)}
  .ad-label{font-size:16px;font-weight:600;line-height:1.05}
  .ad-brand{display:flex;align-items:center;gap:8px}
  .ad-brand-mark{width:22px;height:22px;background:var(--white);border-radius:50%}
  .ad-brand-name{font-size:22px;font-weight:500}
  .ad-brand-by{font-size:9px;font-weight:500;align-self:flex-end;margin-bottom:12px}
</style>
</head>
<body>
<div class="canvas">
  <main class="screen">
    <div class="status-bar">
      <div class="status-left"><span>●●●○○</span><span>NOVA</span>
        <svg width="12" height="9" viewBox="0 0 12 9"><path d="M1 3a7 7 0 0 1 10 0M3 5a4 4 0 0 1 6 0" stroke="#fff" stroke-width="1.4" fill="none"/><circle cx="6" cy="7.5" r="1.1" fill="#fff"/></svg>
      </div>
      <span class="status-time">4:21 PM</span>
      <div class="status-right">
        <svg width="7" height="11" viewBox="0 0 7 11"><path d="M1 3l5 5-2.5 2V1L6 3 1 8" stroke="#fff" stroke-width="1" fill="none"/></svg>
        <span>22%</span>
        <svg width="22" height="10" viewBox="0 0 22 10"><rect x=".5" y=".5" width="19" height="9" rx="2" stroke="#fff" fill="none"/><rect x="2" y="2" width="4" height="6" fill="#fff"/><rect x="20" y="3" width="1.5" height="4" fill="#fff"/></svg>
      </div>
    </div>

    <header class="app-bar">
      <div class="app-bar-top">
        <svg width="20" height="16" viewBox="0 0 20 16"><path d="M19 8H2M8 1L1 8l7 7" stroke="#fff" stroke-width="2" fill="none"/></svg>
        <span class="stop-code">07589</span>
      </div>
      <div class="app-bar-bottom">
        <div class="stop-info">
          <div class="stop-name">Opp rochor ctr</div>
          <div class="stop-street">oppir rd</div>
        </div>
        <div class="stop-actions">
          <svg width="20" height="20" viewBox="0 0 24 24" aria-label="Favourite"><path d="M12 2l3 7 7 .6-5.4 4.7 1.7 7.2L12 17.8 5.7 21.5l1.7-7.2L2 9.6 9 9z" fill="#fff"/></svg>
          <svg width="20" height="20" viewBox="0 0 24 24" aria-label="Refresh"><path d="M5 12a7 7 0 1 0 2.5-5.4" stroke="#fff" stroke-width="2.6" fill="none"/><path d="M4 3v6h6z" fill="#fff"/></svg>
          <svg width="6" height="20" viewBox="0 0 6 20" aria-label="More"><circle cx="3" cy="3" r="2.2" fill="#fff"/><circle cx="3" cy="10" r="2.2" fill="#fff"/><circle cx="3" cy="17" r="2.2" fill="#fff"/></svg>
        </div>
      </div>
    </header>

    <section class="route-grid">
      <div class="column">
        <article class="route-card">
          <div class="route-card-head">
            <svg width="16" height="14" viewBox="0 0 16 14"><rect x="1" y="1" width="14" height="10" rx="2" fill="#fff"/><rect x="3" y="3" width="10" height="3" fill="var(--red)"/><circle cx="4.5" cy="12" r="1.5" fill="#fff"/><circle cx="11.5" cy="12" r="1.5" fill="#fff"/></svg>
            <span class="route-number">120</span>
          </div>
          <div class="arrivals">
            <div class="arrival">
              <div class="arrival-minutes arrival-minutes--next">7</div>
              <div class="arrival-meta">
                <svg class="wab-icon" width="14" height="14" viewBox="0 0 14 14" aria-label="Wheelchair accessible"><circle cx="5" cy="2" r="1.5" fill="#222"/><path d="M5 4v4h4l2 4" stroke="#222" stroke-width="1.6" fill="none"/><circle cx="5.5" cy="9.5" r="3.3" stroke="#222" stroke-width="1.4" fill="none"/></svg>
                <span class="load-dot"></span><span class="load-dot load-dot--red"></span><span class="load-dot"></span>
              </div>
            </div>
            <div class="arrival">
              <div class="arrival-minutes arrival-minutes--later">21</div>
              <div class="arrival-meta">
                <svg class="wab-icon" width="14" height="14" viewBox="0 0 14 14" aria-label="Wheelchair accessible"><circle cx="5" cy="2" r="1.5" fill="#222"/><path d="M5 4v4h4l2 4" stroke="#222" stroke-width="1.6" fill="none"/><circle cx="5.5" cy="9.5" r="3.3" stroke="#222" stroke-width="1.4" fill="none"/></svg>
                <span class="load-dot"></span><span class="load-dot"></span><span class="load-dot load-dot--yellow"></span>
              </div>
            </div>
          </div>
        </article>
        <div class="tile tile--red"><span class="tile-number">131</span><span class="tile-operator">KLT</span></div>
        <div class="tile tile--purple"><span class="tile-number">960</span><span class="tile-operator">VOPN</span></div>
      </div>
      <div class="column">
        <div class="tile tile--red"><span class="tile-number">57</span><span class="tile-operator">KLT</span></div>
        <div class="tile tile--grey"><span class="tile-number">851</span><span class="tile-operator">VOPN</span></div>
        <div class="tile tile--grey"></div>
      </div>
    </section>

    <aside class="ad-banner" role="img" aria-label="Test advertising banner with golden theatre interior">
      <div class="ad-label">320x50<br>Test Banner</div>
      <div class="ad-brand">
        <span class="ad-brand-mark"></span>
        <span class="ad-brand-name">Adverra</span>
        <span class="ad-brand-by">by Trivex</span>
      </div>
    </aside>
  </main>
</div>
</body>
</html>
```